full stationary design for a modern sleek design company

we are a design company that does modern minimalistic interior design works as well as other design services for high end clients.
we need a full stationary design including and not limited to (double sided business card, letter head, envelopes, documents folder...etc) that reflects the modern style design we do.
sleek modern and minimalistic is the requirements.
Updates

please use the latest attached files as there was a slight modification on the logo Added Wednesday, March 1, 2017

minor update on the logo files in JPG and PSD has been updated kindly follow the new attachments. Added Thursday, March 2, 2017

Target Market(s)

modern minimalist clients

Industry/Entity Type

Design Agency

Requirements
Must have
• the logo
Nice to have
• i like the colors in the colored 3D logo attached
Should not have
• too many colors

```html
<!DOCTYPE html>
<html lang="en">
<head>
<meta charset="utf-8">
<title>Linea Atelier Stationery</title>
<link href="https://fonts.googleapis.com/css2?family=Montserrat:wght@400;500;600&display=swap" rel="stylesheet">
<style>
  :root {
    --bg: #efefef;
    --paper: #f7f7f7;
    --charcoal: #3b3b3b;
    --orange: #e8912a;
    --ink: #6a6a6a;
    --light: #e9e9e9;
  }
  * { box-sizing: border-box; margin: 0; padding: 0; }
  html, body { width: 1200px; height: 903px; overflow: hidden; }
  body { background: var(--bg); font-family: "Montserrat", sans-serif; color: var(--ink); position: relative; }
  .piece { position: absolute; overflow: hidden; }
  .piece svg.shape { position: absolute; inset: 0; width: 100%; height: 100%; }

  .brand { display: flex; align-items: center; gap: 5px; font-weight: 600; text-transform: uppercase; letter-spacing: .06em; white-space: nowrap; position: absolute; }
  .brand .mark { background: var(--orange); display: block; }
  .brand--dark { color: var(--charcoal); }
  .brand--light { color: var(--light); }

  /* Letterhead */
  .letterhead { left: 187px; top: 63px; width: 371px; height: 524px; background: var(--paper); }
  .letterhead .brand { left: 34px; top: 40px; font-size: 11px; }
  .letterhead .brand .mark { width: 9px; height: 9px; }
  .contact { position: absolute; font-size: 4.6px; line-height: 7px; color: var(--ink); }
  .contact li { list-style: none; display: flex; align-items: center; gap: 3px; }
  .contact .dot { width: 4px; height: 4px; background: var(--orange); display: inline-block; }
  .letterhead .contact { left: 275px; top: 27px; }
  .web { position: absolute; left: 0; right: 0; text-align: center; font-size: 5px; letter-spacing: .35em; color: #bdbdbd; }
  .letterhead .web { bottom: 10px; }

  /* Folder */
  .folder { left: 623px; top: 38px; width: 437px; height: 553px; background: var(--charcoal); }
  .folder .spine { position: absolute; left: 0; top: 0; bottom: 0; width: 10px; border-right: 1px solid #333; background: #363636; }
  .folder .brand { left: 72px; top: 258px; font-size: 26px; gap: 12px; }
  .folder .brand .mark { width: 24px; height: 24px; }

  /* Business cards */
  .card { width: 166px; height: 96px; }
  .card--front { left: 59px; top: 648px; background: var(--charcoal); }
  .card--front .name { position: absolute; left: 9px; top: 17px; font-size: 5.6px; font-weight: 600; color: var(--orange); }
  .card--front .role { position: absolute; left: 9px; top: 25px; font-size: 4px; color: #cfcfcf; }
  .card--front .contact { left: 9px; top: 34px; font-size: 3.6px; line-height: 5.6px; color: #cfcfcf; }
  .card--front .contact .dot { width: 3px; height: 3px; }
  .card--front .brand { left: 86px; top: 42px; font-size: 6.5px; gap: 3px; }
  .card--front .brand .mark { width: 6px; height: 6px; }
  .card--back { left: 59px; top: 754px; background: var(--charcoal); border-top-right-radius: 16px; }
  .card--back .brand { left: 27px; top: 41px; font-size: 9px; }
  .card--back .brand .mark { width: 9px; height: 9px; }

  /* Envelopes */
  .envelope { width: 415px; height: 198px; background: var(--paper); }
  .envelope--front { left: 265px; top: 648px; }
  .envelope--front .brand { left: 25px; top: 22px; font-size: 10px; }
  .envelope--front .brand .mark { width: 9px; height: 9px; }
  .envelope--front .return { position: absolute; left: 25px; top: 36px; font-size: 4.6px; color: var(--ink); }
  .envelope--front .web { bottom: 7px; }
  .envelope--back { left: 721px; top: 648px; }
  .envelope--back .flap { position: absolute; left: 0; top: 0; width: 100%; height: 70px; background: var(--charcoal); }
  .envelope--back .brand { left: 140px; top: 25px; font-size: 11px; }
  .envelope--back .brand .mark { width: 10px; height: 10px; }
</style>
</head>
<body>

<section class="piece letterhead">
  <svg class="shape" viewBox="0 0 371 524" preserveAspectRatio="none" aria-hidden="true">
    <path d="M0 446 Q185 540 371 446" fill="none" stroke="var(--orange)" stroke-width="2.2"/>
    <path d="M0 451 Q185 545 371 451 L371 524 L0 524 Z" fill="var(--charcoal)"/>
  </svg>
  <div class="brand brand--dark"><span class="mark"></span>Linea Atelier</div>
  <ul class="contact">
    <li>412 Cedar Row</li>
    <li>Juneau, Alaska 99801</li>
    <li><span class="dot"></span>(555) 210 4471</li>
    <li><span class="dot"></span>(555) 318 6620</li>
    <li><span class="dot"></span>adam@lineaatelier.com</li>
  </ul>
  <p class="web">www.lineaatelier.com</p>
</section>

<section class="piece folder">
  <div class="spine"></div>
  <div class="brand brand--light"><span class="mark"></span>Linea Atelier</div>
</section>

<section class="piece card card--front">
  <svg class="shape" viewBox="0 0 166 96" preserveAspectRatio="none" aria-hidden="true">
    <path d="M100 0 Q62 48 100 96 L166 96 L166 0 Z" fill="var(--light)"/>
    <path d="M100 0 Q62 48 100 96" fill="none" stroke="var(--orange)" stroke-width="1.4"/>
  </svg>
  <p class="name">ADAM REYES</p>
  <p class="role">CEO &amp; Founder</p>
  <ul class="contact">
    <li>412 Cedar Row</li>
    <li>Juneau, Alaska 99801</li>
    <li><span class="dot"></span>(555) 210 4471</li>
    <li><span class="dot"></span>(555) 318 6620</li>
    <li><span class="dot"></span>adam@lineaatelier.com</li>
    <li><span class="dot"></span>www.lineaatelier.com</li>
  </ul>
  <div class="brand brand--dark"><span class="mark"></span>Linea Atelier</div>
</section>

<section class="piece card card--back">
  <div class="brand brand--light"><span class="mark"></span>Linea Atelier</div>
</section>

<section class="piece envelope envelope--front">
  <svg class="shape" viewBox="0 0 415 198" preserveAspectRatio="none" aria-hidden="true">
    <path d="M0 100 Q207 228 415 100" fill="none" stroke="var(--orange)" stroke-width="2"/>
    <path d="M0 105 Q207 233 415 105 L415 198 L0 198 Z" fill="var(--charcoal)"/>
  </svg>
  <div class="brand brand--dark"><span class="mark"></span>Linea Atelier</div>
  <p class="return">412 Cedar Row, Juneau, Alaska 99801</p>
  <p class="web">www.lineaatelier.com</p>
</section>

<section class="piece envelope envelope--back">
  <div class="flap"></div>
  <div class="brand brand--light"><span class="mark"></span>Linea Atelier</div>
</section>

</body>
</html>
```